Brookvane Consulting Business Card Design

Business Card Design for Brookvane Consulting. Brookvane Consulting is a boutique consultancy based in Atlanta, GA., that specializes in marketing strategy, organization planning, and leadership development. We provide solutions for small businesses and startups as well as Vantage 300 companies.

http://brookvaneconsulting.com/

Target Market(s)

We provide solutions for small businesses and startups as well as Vantage 300 companies.

Industry/Entity Type

Consulting

Contact Information for Business Card

Two sided business card with priority on contact information, logo, tag line (Inspiration to Dream More, Do More, Become More)

Colors

Designer to choose colors to be used in the design.

Requirements
Must have
• contact information, logo, tag line (Inspiration to Dream More, Do More, Become More)
• Simple no over communication.
Nice to have
• I would like to see different placements of logo and creative use of both sides of the card
Should not have
• Do not put too much information on the card.

```html
<!DOCTYPE html>
<html lang="en">
<head>
<meta charset="utf-8">
<title>Brookvane Consulting — Business Card</title>
<link rel="stylesheet" href="https://fonts.googleapis.com/css2?family=Roboto:wght@400;500&family=Roboto+Condensed:wght@400&display=swap">
<style>
  :root {
    --backdrop: #7b5233;
    --card: #1e1e1f;
    --card-back: #262627;
    --white: #ffffff;
    --name-grey: #c9c9c9;
    --text-light: #e6e6e6;
    --divider: #8c8c8c;
  }
  * { margin: 0; padding: 0; box-sizing: border-box; }
  html, body { width: 1200px; height: 960px; overflow: hidden; }
  body {
    position: relative;
    background: var(--backdrop);
    font-family: "Roboto", Arial, sans-serif;
  }
  .card {
    position: absolute;
    width: 600px;
    height: 343px;
    box-shadow: 0 2px 6px rgba(0,0,0,0.45);
  }
  .card--front { left: 314px; top: 113px; background: var(--card); }
  .card--back { left: 312px; top: 472px; background: var(--card-back); }

  .wordmark {
    position: absolute;
    color: var(--white);
    font-family: "Roboto", Arial, sans-serif;
    font-weight: 400;
    line-height: 1.15;
  }
  .card--front .wordmark { left: 59px; top: 138px; font-size: 29px; width: 230px; }
  .card--back .wordmark { left: 0; width: 100%; top: 110px; font-size: 40px; text-align: center; }

  .divider {
    position: absolute;
    left: 301px; top: 125px;
    width: 1px; height: 92px;
    background: var(--divider);
  }
  .contact { position: absolute; left: 327px; top: 124px; color: var(--text-light); }
  .contact__name {
    font-family: "Roboto Condensed", Arial, sans-serif;
    font-size: 21px; color: var(--name-grey); letter-spacing: 0.3px;
    line-height: 1.1;
  }
  .contact__title { font-size: 15px; font-weight: 500; color: var(--white); margin-top: 3px; }
  .contact__line { font-size: 14px; margin-top: 4px; }
  .contact__line:first-of-type { margin-top: 18px; }

  .band { position: absolute; top: 331px; height: 8px; background: var(--white); }
  .band--left { left: 0; width: 307px; }
  .band--right { left: 546px; width: 54px; }
  .url-tab {
    position: absolute; left: 311px; top: 316px;
    width: 232px; height: 27px;
    background: var(--white); color: #222;
    font-size: 14px; text-align: center; line-height: 27px;
  }

  .grid-texture {
    position: absolute; inset: 0;
    background: var(--card-back);
  }
  .tagline {
    position: absolute; left: 0; width: 100%; top: 281px;
    text-align: center; color: var(--text-light); font-size: 14.5px;
  }
</style>
</head>
<body>
  <section class="card card--front" aria-label="Card front">
    <div class="wordmark">Brookvane<br>Consulting</div>
    <div class="divider"></div>
    <div class="contact">
      <p class="contact__name">DARIO WHITFIELD</p>
      <p class="contact__title">Founder/Managing Director</p>
      <p class="contact__line">P. 424-555-0163</p>
      <p class="contact__line">dario@brookvaneconsulting.com</p>
    </div>
    <div class="band band--left"></div>
    <div class="band band--right"></div>
    <div class="url-tab">www.brookvaneconsulting.com</div>
  </section>

  <section class="card card--back" aria-label="Card back">
    <div class="grid-texture" role="img" aria-label="Faint dark square grid texture"></div>
    <div class="wordmark">Brookvane Consulting</div>
    <p class="tagline">Inspiration to Dream More, Do More, Become More</p>
  </section>
</body>
</html>
```